New Zealand Marlborough Sauvignon Blanc wine packaging design

We need packaging design for our new wine brand, Dunmore Vale. The wine is a New Zealand Marlborough Sauvignon Blanc. We would like the packaging will portray elegance and style with an understated label. We are looking for a label that portrays the elegance of the French Riviera. The label should be round or pill shaped.
Updates

Industry/Entity Type

Wine

Font styles to use
Serif
Sans Serif

Requirements
Must have
• The words in order of importance: Dunmore Vale, Sauvignon Blanc, Marlborough, New Zealand. It should be fit to the bottle posted in the links
Nice to have
• a pill shape or circular shape
Should not have
• Illustrations of wine bottles, wine glasses, or grapes

```html
<!DOCTYPE html>
<html lang="en">
<head>
<meta charset="utf-8">
<title>Dunmore Vale – Sauvignon Blanc Label</title>
<link rel="stylesheet" href="https://fonts.googleapis.com/css2?family=Cormorant+Garamond:wght@500&family=Cormorant+SC:wght@500&family=Playfair+Display+SC:wght@400&display=swap">
<style>
  :root {
    --label-teal: #7a9797;
    --label-white: #ffffff;
    --page-bg: #ffffff;
  }
  html, body {
    margin: 0;
    padding: 0;
    width: 1200px;
    height: 675px;
    overflow: hidden;
    background: var(--page-bg);
  }
  .canvas {
    width: 1200px;
    height: 675px;
    display: flex;
    align-items: center;
    justify-content: center;
  }
  .wine-label {
    width: 560px;
    height: 560px;
    display: block;
  }
  .label-ring { fill: var(--label-teal); }
  .label-inner-line { fill: none; stroke: var(--label-white); stroke-width: 3; }
  .label-field { fill: var(--label-white); }
  .name-band { fill: var(--label-teal); }
  .brand-dot { fill: var(--label-teal); }
  .brand-name {
    font-family: "Playfair Display SC", "Cormorant SC", serif;
    font-size: 50px;
    letter-spacing: 4px;
    fill: var(--label-white);
    text-anchor: middle;
  }
  .varietal {
    font-family: "Cormorant Garamond", serif;
    font-weight: 500;
    font-size: 30px;
    letter-spacing: 3px;
    fill: var(--label-teal);
    text-anchor: middle;
  }
  .region {
    font-family: "Cormorant SC", serif;
    font-weight: 500;
    font-size: 13px;
    letter-spacing: 3px;
    fill: var(--label-teal);
    text-anchor: middle;
  }
</style>
</head>
<body>
<main class="canvas">
  <svg class="wine-label" viewBox="-280 -280 560 560" role="img" aria-label="Dunmore Vale Sauvignon Blanc, Marlborough, New Zealand round wine label">
    <defs>
      <clipPath id="label-field-clip">
        <circle cx="0" cy="0" r="214"/>
      </clipPath>
    </defs>
    <circle class="label-ring" cx="0" cy="0" r="270"/>
    <circle class="label-inner-line" cx="0" cy="0" r="221"/>
    <circle class="label-field" cx="0" cy="0" r="214"/>
    <rect class="name-band" x="-230" y="-51" width="460" height="132" clip-path="url(#label-field-clip)"/>
    <circle class="brand-dot" cx="0" cy="-132" r="49"/>
    <text class="brand-name" x="0" y="9">DUNMORE</text>
    <text class="brand-name" x="0" y="58">VALE</text>
    <text class="varietal" x="0" y="122">Sauvignon Blanc</text>
    <text class="region" x="0" y="150">Marlborough, New Zealand</text>
  </svg>
</main>
</body>
</html>
```